Poster for Kirtan Music Event

Design (3) 24" x 36" Posters

I have provided a sample a friend did in Australia: ( Picture No. 4 )

Use all the text on sample poster except the replacement changes below.

Replace with the following text as this is for different location:
Replacement Text:

Every Friday Night 7:00pm-8:30pm
Kealoha Pilates & Movement Studio
947 Hollister Rd Paia

Free Kirtan Experience! or Free Event
Mohan Priya Sevi & Companions

Optional Text:

A evening of music, singing of spiritual mantras, and refreshments

Bring flowers, musical instruments, friends, or just come with an open heart.

Meditate on transcendental sounds that provide rest for the mind & heart"

An evening of music & singing of sacred mantra's

```html
<!DOCTYPE html>
<html lang="en">
<head>
<meta charset="utf-8">
<title>Kirtan Experience – Poster</title>
<link rel="stylesheet" href="https://fonts.googleapis.com/css2?family=Arimo:ital,wght@1,700&family=Cinzel:wght@700;900&family=Oswald:wght@300;400;600;700&family=Russo+One&display=swap">
<style>
  :root {
    --frame: #f3e9ea;
    --deep-red: #8e1a22;
    --red: #b82a2c;
    --warm-red: #d0432f;
    --orange: #f08a2c;
    --glow: #ffd27a;
    --maroon: #5e1216;
    --band-yellow: #c9b020;
    --lime: #a7b21f;
    --tangerine: #e27a1d;
    --white: #ffffff;
    --title-red: #a3161f;
  }
  * { box-sizing: border-box; margin: 0; padding: 0; }
  html, body { width: 800px; height: 1200px; overflow: hidden; background: #ffffff; }

  .poster {
    position: relative;
    width: 800px;
    height: 1200px;
    overflow: hidden;
    border: 10px solid var(--frame);
    box-shadow: inset 0 0 18px rgba(0,0,0,0.45);
    background:
      radial-gradient(circle at 50% 49%, var(--glow) 0, var(--orange) 14%, var(--warm-red) 42%, var(--red) 62%, var(--deep-red) 100%);
  }

  .sun-band { position: absolute; inset: 0; }

  .mandala {
    position: absolute;
    left: 124px;
    top: 302px;
    width: 552px;
    height: 552px;
    border-radius: 50%;
    background: radial-gradient(circle, #fff2c4 0, #ffc066 18%, #f39a3e 38%, #e8602f 58%, #c9302c 76%, rgba(180,40,40,0) 100%);
    opacity: 0.9;
  }

  .tag {
    position: absolute;
    left: 262px;
    top: 26px;
    width: 264px;
    height: 84px;
    background: rgba(110, 18, 26, 0.75);
    color: var(--white);
    font: 700 40px/84px "Oswald", sans-serif;
    text-align: center;
    letter-spacing: 0.5px;
    text-shadow: 0 2px 3px rgba(0,0,0,0.4);
  }

  .title {
    position: absolute;
    left: 0;
    right: 0;
    top: 180px;
    text-align: center;
    white-space: nowrap;
    font: 400 54px/80px "Russo One", sans-serif;
    letter-spacing: 0;
    color: #f4f4f4;
    -webkit-text-stroke: 2.5px var(--title-red);
    paint-order: stroke fill;
    text-shadow: 0 0 10px rgba(255,255,255,0.7);
    transform: scaleY(1.5);
    transform-origin: 50% 50%;
  }

  .free-badge {
    position: absolute;
    left: 585px;
    top: 332px;
    width: 124px;
    height: 124px;
    border-radius: 50%;
    background: rgba(80, 14, 18, 0.85);
    color: var(--white);
    text-align: center;
    font-family: "Oswald", sans-serif;
    padding-top: 18px;
  }
  .free-badge .big { display: block; font-weight: 700; font-size: 48px; line-height: 50px; }
  .free-badge .small { display: block; font-weight: 600; font-size: 25px; line-height: 28px; }

  .schedule {
    position: absolute;
    left: 0;
    right: 0;
    top: 548px;
    height: 100px;
    background: rgba(255, 235, 235, 0.42);
    text-align: center;
  }
  .schedule .stars {
    position: absolute;
    left: 0;
    right: 0;
    color: var(--title-red);
    font-size: 13px;
    letter-spacing: 6px;
    line-height: 14px;
  }
  .schedule .stars.top { top: 8px; }
  .schedule .stars.bottom { bottom: 8px; }
  .schedule .when {
    font: 700 42px/100px "Cinzel", serif;
    font-variant: small-caps;
    color: var(--title-red);
    letter-spacing: 0.5px;
    white-space: nowrap;
    text-shadow: 0 1px 0 rgba(255,255,255,0.5);
  }

  .note {
    position: absolute;
    color: var(--white);
    font: italic 700 16px/21px "Arimo", sans-serif;
    border: 3px solid #f6dede;
    border-radius: 6px 44px 6px 44px;
    box-shadow: 0 2px 6px rgba(0,0,0,0.25);
    white-space: nowrap;
  }
  .note.green {
    left: 55px; top: 734px; width: 254px; height: 132px;
    background: var(--lime);
    padding: 18px 10px 0 14px;
  }
  .note.orange {
    left: 230px; top: 884px; width: 252px; height: 131px;
    background: var(--tangerine);
    padding: 30px 10px 0 44px;
  }

  .divider {
    position: absolute;
    left: 270px;
    top: 1022px;
    width: 260px;
    height: 36px;
  }

  .venue {
    position: absolute;
    left: 0;
    right: 0;
    top: 1062px;
    text-align: center;
    color: var(--white);
    font: 400 26px/38px "Oswald", sans-serif;
    font-style: normal;
    letter-spacing: 0.3px;
  }

  .hosts {
    position: absolute;
    left: 0;
    right: 0;
    top: 1140px;
    text-align: center;
    color: var(--white);
    font: 300 19px/26px "Oswald", sans-serif;
    letter-spacing: 0.5px;
  }
</style>
</head>
<body>
  <main class="poster">
    <svg class="sun-band" width="780" height="1180" viewBox="0 0 780 1180" aria-hidden="true">
      <polygon points="0,150 780,100 780,300 0,330" fill="var(--band-yellow)" opacity="0.55"/>
      <polygon points="0,0 780,0 780,100 0,150" fill="var(--maroon)" opacity="0.25"/>
      <polygon points="0,1180 0,1050 260,1180" fill="var(--maroon)" opacity="0.2"/>
    </svg>

    <div class="mandala" role="img" aria-label="Radiant orange lotus mandala with sunburst rays"></div>

    <div class="tag">MUSIC EVENT</div>

    <h1 class="title">KIRTAN EXPERIENCE</h1>

    <div class="free-badge">
      <span class="big">FREE</span>
      <span class="small">EVENT!</span>
    </div>

    <section class="schedule">
      <div class="stars top">★★★</div>
      <p class="when">Every Friday Night 7:00pm-8:30pm</p>
      <div class="stars bottom">★★★</div>
    </section>

    <p class="note green">Join us in the singing of<br>transcendental sounds<br>that provide rest for the<br>mind &amp; heart</p>

    <p class="note orange">An evening of<br>music &amp; singing<br>of sacred mantra's</p>

    <svg class="divider" viewBox="0 0 260 36" aria-hidden="true">
      <polygon points="130,2 133.5,10 142,10 135,15 138,23 130,18 122,23 125,15 118,10 126.5,10" fill="var(--white)"/>
      <line x1="4" y1="26" x2="256" y2="26" stroke="var(--white)" stroke-width="1.5"/>
      <line x1="60" y1="33" x2="200" y2="33" stroke="var(--white)" stroke-width="1.5"/>
    </svg>

    <address class="venue">
      Kealoha Pilates &amp; Movement Studio<br>
      947 Hollister Rd Paia
    </address>

    <p class="hosts">Mohan Priya Sevi &amp; Companions</p>
  </main>
</body>
</html>
```